Lumarind Label Design

We need a label design for our cream dispenser. Its a cream against acne called Lumarind, Works with its active ingredients of silver and oxygen. We are looking for a flashy / colorful and modern design .

Target Market(s)

young people / People with acne

Industry/Entity Type

Skin Care Product

Colors

Designer to choose colors to be used in the design.

Requirements
Must have
• be modern, Colours
• -THE DESIGN NEEDS TO BE 10,7x7 , ITS 1 BIG STICKER THAT RAPS AROUND THE BOTTLE

```html
<!DOCTYPE html>
<html lang="en">
<head>
<meta charset="utf-8">
<title>Lumarind Acne Repair &amp; Care Label</title>
<link rel="stylesheet" href="https://fonts.googleapis.com/css2?family=Outfit:wght@400;500;600&display=swap">
<style>
  :root {
    --page-bg: #f4f5f6;
    --label-white: #ffffff;
    --teal: #23bec4;
    --green-mid: #5cb040;
    --green-light: #a6d45a;
    --ink-grey: #4a545a;
    --text-white: #ffffff;
  }
  * { box-sizing: border-box; margin: 0; padding: 0; }
  html, body { width: 1200px; height: 1200px; overflow: hidden; }
  body {
    background: var(--page-bg);
    font-family: "Outfit", sans-serif;
    position: relative;
  }
  .label {
    position: absolute;
    left: 65px;
    top: 250px;
    width: 1070px;
    height: 700px;
    background: var(--label-white);
    overflow: hidden;
    box-shadow: 0 6px 24px rgba(0,0,0,0.08);
  }
  .label-art { position: absolute; inset: 0; }
  .maker {
    position: absolute;
    top: 70px; left: 0; right: 0;
    display: flex; justify-content: center; align-items: center; gap: 12px;
    font-size: 26px; font-weight: 500; letter-spacing: 2px;
    color: var(--ink-grey);
  }
  .maker-square { width: 18px; height: 18px; background: var(--teal); }
  .brand-name {
    position: absolute;
    top: 125px; left: 0; right: 0;
    text-align: center;
    font-size: 72px; font-weight: 600; letter-spacing: 8px;
    color: var(--ink-grey);
  }
  .product-claim {
    position: absolute;
    top: 405px; left: 0; right: 0;
    text-align: center;
    font-size: 42px; font-weight: 500; line-height: 1.15;
    color: var(--text-white);
  }
  .cream-visual {
    position: absolute;
    left: 440px; top: 535px;
    width: 190px; height: 100px;
    border-radius: 50%;
    background: radial-gradient(ellipse at 50% 45%, #ffffff 0%, #eef6f7 60%, #d6eef0 100%);
  }
  .volume {
    position: absolute;
    bottom: 18px; left: 0; right: 0;
    text-align: center;
    font-size: 17px; font-weight: 500;
    color: var(--text-white);
  }
</style>
</head>
<body>
  <main class="label">
    <svg class="label-art" viewBox="0 0 1070 700" preserveAspectRatio="none" aria-hidden="true">
      <rect width="1070" height="700" fill="var(--label-white)"/>
      <path d="M0 320 Q535 300 1070 250 L1070 700 L0 700 Z" fill="var(--green-light)"/>
      <path d="M0 342 Q535 322 1070 272 L1070 700 L0 700 Z" fill="var(--green-mid)"/>
      <path d="M0 364 Q535 344 1070 294 L1070 700 L0 700 Z" fill="var(--teal)"/>
    </svg>
    <div class="maker"><span class="maker-square"></span>Lumarind Labs</div>
    <h1 class="brand-name">Lumarind</h1>
    <p class="product-claim">ACNE REPAIR<br>&amp; CARE</p>
    <div class="cream-visual" role="img" aria-label="Swirl of white cream with soft white feathers"></div>
    <p class="volume">100 ML</p>
  </main>
</body>
</html>
```